Redesign of business card for Cedar Ridge Mechanical

We are looking for a new design for our business cards for Cedar Ridge Mechanical. We are a plumbing & HVAC construction company, operating on the West Coast of Canada and USA. Logo attached.
Industry/Entity Type
Construction - Plumbing & HVAC
Contact Information for Business Card
Name, address, phone numbers, email, website address
Look and feel
Each slider illustrates characteristics of the customer's brand and the style your logo design should communicate.

```html
<!DOCTYPE html>
<html lang="en">
<head>
<meta charset="utf-8">
<title>Cedar Ridge Mechanical – Business Card</title>
<link href="https://fonts.googleapis.com/css2?family=Montserrat:wght@400;500;600;700&display=swap" rel="stylesheet">
<style>
  :root {
    --backdrop: #e9e6e1;
    --card-light: #ffffff;
    --card-dark: #2b2b2b;
    --ink: #1f1f1f;
    --ink-soft: #333333;
    --band-dark: #262626;
    --band-grey: #5f5f5f;
    --on-dark: #ffffff;
  }
  * { box-sizing: border-box; margin: 0; padding: 0; }
  html, body {
    width: 900px; height: 1200px; overflow: hidden;
    background: var(--backdrop);
    font-family: "Montserrat", Arial, sans-serif;
  }
  .stage { position: relative; width: 900px; height: 1200px; }
  .card {
    position: absolute; left: 80px; width: 742px; height: 442px;
    border-radius: 22px; overflow: hidden;
    box-shadow: 0 6px 18px rgba(0,0,0,.25);
  }
  .card--front { top: 130px; background: var(--card-light); }
  .card--back { top: 638px; background: var(--card-dark); }

  .brand {
    position: absolute; left: 0; right: 0;
    display: flex; align-items: center; justify-content: center; gap: 16px;
    font-weight: 700; letter-spacing: 2px; font-size: 30px;
  }
  .brand__mark { width: 26px; height: 26px; }
  .card--front .brand { top: 118px; color: var(--ink); }
  .card--front .brand__mark { background: var(--ink); }
  .card--back .brand { top: 200px; color: var(--on-dark); font-size: 34px; }
  .card--back .brand__mark { background: var(--on-dark); width: 30px; height: 30px; }

  .person {
    position: absolute; right: 410px; top: 272px; text-align: right; color: var(--ink);
  }
  .person__name { font-size: 24px; font-weight: 700; line-height: 1.2; }
  .person__role { font-size: 15px; font-weight: 500; margin-top: 4px; color: var(--ink-soft); }
  .divider {
    position: absolute; left: 356px; top: 268px; width: 2px; height: 82px; background: var(--ink);
  }
  .contacts { position: absolute; left: 376px; top: 264px; list-style: none; }
  .contacts li {
    display: flex; align-items: center; gap: 10px;
    font-size: 15.5px; color: var(--ink); height: 30px;
  }
  .contacts svg { width: 15px; height: 15px; fill: var(--ink); flex: none; }

  .address-band { position: absolute; left: 0; top: 372px; width: 742px; height: 35px; }
  .address-band__text {
    position: absolute; right: 244px; top: 372px; height: 35px; line-height: 35px;
    color: var(--on-dark); font-size: 16px;
  }
</style>
</head>
<body>
<main class="stage">
  <section class="card card--front">
    <div class="brand"><span class="brand__mark"></span>CEDAR RIDGE MECHANICAL</div>

    <div class="person">
      <p class="person__name">Daniel Hart</p>
      <p class="person__role">Managing Director</p>
    </div>
    <div class="divider"></div>
    <ul class="contacts">
      <li>
        <svg viewBox="0 0 24 24"><path d="M6.6 10.8a15.1 15.1 0 0 0 6.6 6.6l2.2-2.2a1 1 0 0 1 1-.25 11.4 11.4 0 0 0 3.6.57 1 1 0 0 1 1 1V20a1 1 0 0 1-1 1A17 17 0 0 1 3 4a1 1 0 0 1 1-1h3.5a1 1 0 0 1 1 1c0 1.25.2 2.45.57 3.57a1 1 0 0 1-.25 1z"/></svg>
        555.210.4477
      </li>
      <li>
        <svg viewBox="0 0 24 24"><path d="M2 5h20v14H2zm2 2v.5l8 5 8-5V7l-8 5z"/></svg>
        info@cedarridgemechanical.com
      </li>
      <li>
        <svg viewBox="0 0 24 24"><path d="M12 2a10 10 0 1 0 0 20 10 10 0 0 0 0-20zm-1 17.9A8 8 0 0 1 4.1 11H7v2l4 4zm6.9-2.5A2 2 0 0 0 16 16h-1v-3a1 1 0 0 0-1-1H8v-2h2a1 1 0 0 0 1-1V7h2a2 2 0 0 0 2-2v-.4a8 8 0 0 1 2.9 12.8z"/></svg>
        www.cedarridgemechanical.com
      </li>
    </ul>

    <svg class="address-band" viewBox="0 0 742 35" aria-hidden="true">
      <polygon points="0,0 544,0 526,35 0,35" fill="var(--band-dark)"/>
      <polygon points="554,0 742,0 742,35 536,35" fill="var(--band-grey)"/>
    </svg>
    <p class="address-band__text">240 Birch Hollow Road Fairview, OR 97024</p>
  </section>

  <section class="card card--back">
    <div class="brand"><span class="brand__mark"></span>CEDAR RIDGE MECHANICAL</div>
  </section>
</main>
</body>
</html>
```